Design letter head and business card

Hello,

you should design a business card and letter paper for Kranichflug Marketing. In German we write this word with K insteat of C.

Company does not have a logo. But in general, we write Kranichflug Marketing in 2 lines.
First line red: KRANICHFLUG
Second line gray: MARKETING

Red (or wine red) and Gray / Black are our favorite colors.

Company slogan: "Fresh Ground Online Marketing".

Company offers SEO, SEM, SEA, AdWords, Conversion Optimization, Online Markting Consulting ...

The website is old, please do not use this as base for your task.

German letter paper sizes:
Viawable Dimensions : 210 x 297 mm
Needed file dimensions: 212 x 299 mm

Informations to include:

Address:
Kranichflug Marketing GmbH
Lindenweg 23
71592 Weinstadt
Germany

Geschäftsführer | CEO: Bernhard Olzner

Phone: +49 (0) 7151 846 27 05

Fax: +49 (0) 7151 846 27 88

Mail: info@kranichflug-beispiel.de

Web: www.kranichflug-beispiel.de

Amtsgericht Suttgart, HRB 537264

Bank: Rosenauer Bank
IBAN: DE827315480900XXXXXXXX
BIC: GENODES1RSQ

Thanks

Bernhard

Target Market(s)

People who likes to win the online marketing game.

Industry/Entity Type

Business

Contact Information for Business Card

Here is the personal text on the card:

Name:
Bernhard Olzner

Title:
Geschäftsführer | CEO

Address:
Kranichflug Marketing GmbH
Lindenweg 23
71592 Weinstadt
Germany

Phone:
+49 (0) 7151 846 27 05

Fax:
+49 (0) 7151 846 27 88

Mail:
olzner@kranichflug-beispiel.de

Web:
www.kranichflug-beispiel.de

Business Card:
Viewable Dimensions: 85 x 55 mm
Needed file dimensions: 87 x 57mm

Font styles to use
Sans Serif

Requirements
Nice to have
• It would be great to see the dynamics of a helicopter.

```html
<!DOCTYPE html>
<html lang="de">
<head>
<meta charset="utf-8">
<title>Kranichflug Marketing – Visitenkarte</title>
<link rel="stylesheet" href="https://fonts.googleapis.com/css2?family=Abel&family=Oswald:wght@600&display=swap">
<style>
  :root {
    --panel-light: #e6e6e8;
    --panel-wine: #8e1f22;
    --ink-dark: #3a3a3a;
    --ink-wine: #8e1f22;
    --ink-light: #f2f2f2;
    --logo-grey: #c9c9cb;
    --mark-tone-a: #bdbdbd;
    --mark-tone-b: #6e6e6e;
  }
  html, body {
    margin: 0;
    padding: 0;
    width: 1200px;
    height: 667px;
    overflow: hidden;
    background: #ffffff;
  }
  .card {
    position: relative;
    width: 1200px;
    height: 667px;
    overflow: hidden;
    font-family: "Abel", "Arial Narrow", sans-serif;
  }
  .card__side-light {
    position: absolute;
    left: 0; top: 0;
    width: 647px; height: 667px;
    background: var(--panel-light);
  }
  .card__side-wine {
    position: absolute;
    left: 647px; top: 0;
    width: 553px; height: 667px;
    background: var(--panel-wine);
  }
  .person {
    position: absolute;
    left: 59px;
    top: 248px;
  }
  .person__name {
    margin: 0;
    font-family: "Oswald", "Arial Narrow", sans-serif;
    font-weight: 600;
    font-size: 40px;
    line-height: 48px;
    color: var(--ink-wine);
  }
  .person__title {
    margin: 0;
    font-size: 36px;
    line-height: 44px;
    color: var(--ink-dark);
  }
  .contact {
    position: absolute;
    left: 59px;
    top: 478px;
    margin: 0;
    font-size: 36px;
    line-height: 49px;
    color: var(--ink-dark);
    font-style: normal;
  }
  .address {
    position: absolute;
    right: 55px;
    top: 471px;
    margin: 0;
    font-size: 36px;
    line-height: 50px;
    color: var(--ink-light);
    text-align: right;
    font-style: normal;
  }
  .brand {
    position: absolute;
    right: 56px;
    top: 45px;
    text-align: right;
  }
  .brand__mark {
    display: block;
    margin: 0 20px 6px auto;
    width: 130px;
    height: 107px;
  }
  .brand__name {
    margin: 0;
    font-family: "Oswald", "Arial Narrow", sans-serif;
    font-weight: 600;
    font-size: 32px;
    line-height: 33px;
    letter-spacing: 0.5px;
    color: var(--logo-grey);
  }
  .brand__slogan {
    margin: 6px 0 0;
    font-size: 18px;
    line-height: 22px;
    color: var(--ink-light);
  }
</style>
</head>
<body>
<main class="card">
  <div class="card__side-light"></div>
  <div class="card__side-wine"></div>

  <section class="person">
    <h1 class="person__name">Bernhard Olzner</h1>
    <p class="person__title">Geschäftsführer | CEO</p>
  </section>

  <address class="contact">
    Phone: +49 (0) 7364 846 27 05<br>
    Fax: +49 (0) 7364 846 27 88<br>
    E-mail: info@kranichflug-beispiel.de
  </address>

  <header class="brand">
    <svg class="brand__mark" role="img" aria-label="Illustration of a flying aircraft" viewBox="0 0 130 107">
      <defs>
        <radialGradient id="markTone" cx="50%" cy="50%" r="50%">
          <stop offset="0%" stop-color="var(--mark-tone-a)"/>
          <stop offset="100%" stop-color="var(--mark-tone-b)" stop-opacity="0"/>
        </radialGradient>
      </defs>
      <ellipse cx="65" cy="53" rx="64" ry="52" fill="url(#markTone)" opacity="0.55"/>
    </svg>
    <p class="brand__name">KRANICHFLUG<br>MARKETING</p>
    <p class="brand__slogan">Fresh Ground Online Marketing</p>
  </header>

  <address class="address">
    Kranichflug Marketing GmbH,<br>
    Lindenweg 23,<br>
    71592 Talbrunn, Germany
  </address>
</main>
</body>
</html>
```